The logo name is "Harbor Skin". The name of the product will be "Cutaneous Comfort". This product is specifically formulated for amputees. Therefore under the product name it should state "for amputees". The catch phrase will be "Experience Harbor find Calmness"
These are the things we need on the label:
Logo, product name, "for amputees", "Experience Harbor find Calmness", Safe, Effective, Directions: spray on problem areas, no need to dry off. harborskin.example, Made in Canada, 500ml.
The MOST IMPORTANT and therefore the most prominent thing on this lable will be the LOGO! The second most prominent thing will be the word "Comfort" We want to keep it very plain, very simple, very unclutered. Keep in mind that this lable will be placed on a white bottle or have a white back ground. The 500ml white PE bottle with trigger sprayer will have a tear drop label. See attached die line (S-294).
We want to stay with the colours that goes with the colour scheme of the logo. See attached logo. Soft colours. We do not want a picture! We would like the lable to be classy and rich.
Updates
The logo name is "Harbor Skin". The name of the product will be "Cutaneous Comfort". This product is specificlly formulated for amputees. Therefore under the product name it should state "for amputees". The catch phrase will be "Experience Harbor find Calmness"
Logo, product name, "for amputees", catch phrase "Experience Harbor find Calmness", Clean, Safe, Effective, Directions: spray on problem areas, no need to dry off. Also Harbor Skin Corpation, harborskin.example, Made in Canada, 500ml.
We want to stay with the colour scheme of the logo. See attached logo. Soft colours. We do not want a picture! We would like the lable to be classy and rich.
This is the offical directive that came from the governing panal of this lable. This panal it not know where it wanted to take this lable that would represent this line until they review all of your submissions, thank you for all your talented hard work. But now it is clear it is time to regroup and hit this objective.
Project Deadline Extended
Reason: New restrictions on lable wording for this product.
Target Market(s)
Amputees and Parents of.
Industry/Entity Type
Product
Requirements
Must have
- Final product to be in a pdf or an illustrator file

```html
<!DOCTYPE html>
<html lang="en">
<head>
<meta charset="utf-8">
<title>Harbor Skin – Cutaneous Comfort Label, Front</title>
<link href="https://fonts.googleapis.com/css2?family=Libre+Baskerville:wght@400;700&family=Merriweather:wght@900&family=Nunito:wght@800&family=Open+Sans:wght@600;700&family=Oswald:wght@500&display=swap" rel="stylesheet">
<style>
  :root {
    --page: #ffffff;
    --label-mist: #dcebe8;
    --label-white: #ffffff;
    --die-line: #8f9b98;
    --teal: #1f8a70;
    --forest: #0f3b2b;
    --amber: #f7a12c;
    --ink: #1c2a26;
  }
  html, body {
    margin: 0;
    width: 1200px;
    height: 900px;
    overflow: hidden;
    background: var(--page);
  }
  .label-sheet { display: block; width: 1200px; height: 900px; }
  .band-mist { fill: var(--label-mist); }
  .band-white { fill: var(--label-white); }
  .die-outline { fill: none; stroke: var(--die-line); stroke-width: 1.2; }
  .claim-dot { fill: var(--teal); }
  .claim-word { font-family: "Nunito", sans-serif; font-weight: 800; font-size: 13px; fill: var(--teal); }
  .tagline { font-family: "Nunito", sans-serif; font-weight: 800; font-size: 14px; fill: var(--teal); }
  .brand-square { fill: var(--teal); }
  .brand-name { font-family: "Libre Baskerville", serif; font-weight: 400; font-size: 40px; fill: var(--forest); }
  .product-line { font-family: "Merriweather", serif; font-weight: 900; font-size: 29px; fill: var(--teal); }
  .product-name { font-family: "Libre Baskerville", serif; font-weight: 700; font-size: 46px; fill: var(--forest); }
  .audience-pill { fill: var(--amber); stroke: var(--label-white); stroke-width: 2; }
  .audience-text { font-family: "Nunito", sans-serif; font-weight: 800; font-size: 17px; fill: var(--label-white); }
  .fine-print { font-family: "Open Sans", sans-serif; font-weight: 700; font-size: 7.5px; fill: var(--ink); }
  .fine-print-small { font-family: "Open Sans", sans-serif; font-weight: 600; font-size: 6.5px; fill: var(--ink); }
  .volume { font-family: "Oswald", sans-serif; font-weight: 500; font-size: 13px; fill: var(--ink); }
  .panel-caption { font-family: "Open Sans", sans-serif; font-weight: 700; font-size: 14px; fill: var(--ink); }
</style>
</head>
<body>
<svg class="label-sheet" viewBox="0 0 1200 900" xmlns="http://www.w3.org/2000/svg">
  <defs>
    <clipPath id="teardrop-die">
      <path d="M660 103 Q674 100 688 104 C740 200 785 420 782 570 C781 650 778 700 770 740 Q766 752 755 752 L440 752 Q428 752 424 740 C416 690 415 640 416 575 C420 420 520 230 660 103 Z"/>
    </clipPath>
  </defs>

  <g class="label-body" clip-path="url(#teardrop-die)">
    <rect class="band-mist" x="400" y="95" width="400" height="244"/>
    <rect class="band-white" x="400" y="339" width="400" height="251"/>
    <rect class="band-mist" x="400" y="590" width="400" height="170"/>
  </g>
  <path class="die-outline" d="M660 103 Q674 100 688 104 C740 200 785 420 782 570 C781 650 778 700 770 740 Q766 752 755 752 L440 752 Q428 752 424 740 C416 690 415 640 416 575 C420 420 520 230 660 103 Z"/>

  <g class="product-claims">
    <text class="claim-word" x="668" y="152" text-anchor="middle">Safe</text>
    <circle class="claim-dot" cx="668" cy="171" r="11"/>
    <text class="claim-word" x="668" y="201" text-anchor="middle">Effective</text>
  </g>

  <g class="catch-phrase">
    <text class="tagline" x="650" y="244" text-anchor="middle">Experience Harbor</text>
    <text class="tagline" x="650" y="264" text-anchor="middle">Find Calmness</text>
  </g>

  <g class="brand-mark">
    <rect class="brand-square" x="497" y="373" width="50" height="50"/>
    <text class="brand-name" x="560" y="418" textLength="195" lengthAdjust="spacingAndGlyphs">Harbor Skin</text>
  </g>

  <g class="product-title">
    <text class="product-line" x="612" y="513" text-anchor="middle" textLength="180" lengthAdjust="spacingAndGlyphs">Cutaneous</text>
    <text class="product-name" x="612" y="564" text-anchor="middle" textLength="200" lengthAdjust="spacingAndGlyphs">COMFORT</text>
    <ellipse class="audience-pill" cx="613" cy="591" rx="89" ry="17"/>
    <text class="audience-text" x="613" y="597" text-anchor="middle">For Amputees</text>
  </g>

  <g class="label-footer">
    <text class="fine-print" x="461" y="707">DIRECTIONS:</text>
    <text class="fine-print" x="461" y="716">Spray on problem areas,</text>
    <text class="fine-print" x="461" y="725">no need to dry off.</text>
    <text class="volume" x="604" y="718" text-anchor="middle">500mL</text>
    <text class="fine-print" x="656" y="706">Harbor Skin Corporation</text>
    <text class="fine-print" x="656" y="715">www.harborskin.example</text>
    <text class="fine-print-small" x="656" y="731">MADE IN CANADA</text>
  </g>

  <text class="panel-caption" x="604" y="792" text-anchor="middle">Front</text>
</svg>
</body>
</html>
```